Coastline Premier Retreats Business Card Design

Design a business card for Coastline Premier Retreats. Look at the website for colors and reference. Card should have logo, name, title, office number, mobile number, email, URL and a tagline like, "Luxury Hotel & Resort Email Marketing" (This might change).

https://www.coastlinepremierretreats.example

The rest I will leave up to your imagination.

Contact Information for Business Card

Logo, name, title, office number, mobile number, email, URL and a tagline like, "Luxury Hotel & Resort Email Marketing" (This might change).

```html
<!DOCTYPE html>
<html lang="en">
<head>
<meta charset="utf-8">
<title>Coastline Premier Retreats – Business Card</title>
<link rel="stylesheet" href="https://fonts.googleapis.com/css2?family=Archivo:wght@400;700&display=swap">
<style>
  :root {
    --bg: #e6e4e1;
    --orange: #e56b05;
    --ink: #0b0b0b;
    --paper: #f4f4f4;
    --white: #ffffff;
    --grey-text: #2a2a2a;
    --gold: #f3b64a;
  }
  * { margin: 0; padding: 0; box-sizing: border-box; }
  html, body {
    width: 1200px; height: 960px; overflow: hidden;
    background: var(--bg);
    font-family: "Archivo", Arial, sans-serif;
  }
  .canvas { position: relative; width: 1200px; height: 960px; }

  .card {
    position: absolute;
    width: 600px; height: 343px;
    border-radius: 22px;
    overflow: hidden;
    box-shadow: 0 10px 28px rgba(0,0,0,0.18);
  }

  /* Back side */
  .card-back {
    left: 300px; top: 90px;
    background: var(--orange);
    display: flex; align-items: center; justify-content: center;
  }
  .card-back .brand-name {
    font-weight: 700;
    font-size: 30px;
    letter-spacing: 2px;
    color: var(--gold);
    text-transform: uppercase;
  }

  /* Front side */
  .card-front {
    left: 300px; top: 520px;
    background: var(--paper);
  }
  .contact-panel {
    position: absolute;
    left: 200px; top: 0;
    width: 300px; height: 205px;
    background: var(--ink);
    color: var(--white);
    padding-top: 30px;
    text-align: center;
  }
  .person-name {
    color: var(--orange);
    font-weight: 700;
    font-size: 22px;
    letter-spacing: 0.5px;
  }
  .person-title {
    font-size: 14px;
    margin-top: 2px;
  }
  .contact-list {
    list-style: none;
    margin-top: 18px;
    display: inline-block;
    text-align: left;
    font-size: 14.5px;
    line-height: 20px;
  }
  .contact-list li { display: flex; align-items: center; gap: 7px; white-space: nowrap; }
  .contact-list li.phone { padding-left: 60px; }
  .contact-list svg { width: 13px; height: 13px; flex: none; }

  .logo-row {
    position: absolute;
    left: 200px; top: 222px;
    width: 300px; height: 50px;
    display: flex; align-items: center; justify-content: center; gap: 10px;
  }
  .logo-row .mark {
    width: 14px; height: 14px; background: var(--orange);
  }
  .logo-row .brand-name {
    font-weight: 700;
    font-size: 17px;
    letter-spacing: 1px;
    color: var(--ink);
    text-transform: uppercase;
    white-space: nowrap;
  }
  .tagline {
    position: absolute;
    left: 185px; top: 290px;
    font-size: 16px;
    color: var(--grey-text);
  }
</style>
</head>
<body>
<main class="canvas">

  <section class="card card-back" aria-label="Card back">
    <span class="brand-name">Coastline Premier Retreats</span>
  </section>

  <section class="card card-front" aria-label="Card front">
    <div class="contact-panel">
      <h1 class="person-name">Daniel Reeve</h1>
      <p class="person-title">President</p>
      <ul class="contact-list">
        <li class="phone">
          <svg viewBox="0 0 16 16" aria-hidden="true"><path fill="var(--orange)" d="M3.6 1.2l2.2 2.6-1.3 1.6c.9 2 2.6 3.7 4.6 4.6l1.6-1.3 2.6 2.2-1.4 2.2C7 13 3 9 1.3 3z"/></svg>
          555.014.2000
        </li>
        <li class="phone">
          <svg viewBox="0 0 16 16" aria-hidden="true"><rect x="4" y="1" width="8" height="14" rx="1.5" fill="none" stroke="var(--orange)" stroke-width="1.6"/><circle cx="8" cy="12.5" r="0.9" fill="var(--orange)"/></svg>
          555.014.2001
        </li>
        <li>
          <svg viewBox="0 0 16 16" aria-hidden="true"><rect x="1" y="3" width="14" height="10" fill="var(--orange)"/><path d="M1 3l7 6 7-6" fill="none" stroke="var(--ink)" stroke-width="1.2"/></svg>
          info@coastlinepremierretreats.example
        </li>
        <li>
          <svg viewBox="0 0 16 16" aria-hidden="true"><circle cx="8" cy="8" r="7" fill="var(--orange)"/><path d="M1 8h14M8 1c-3 3.5-3 10.5 0 14M8 1c3 3.5 3 10.5 0 14" fill="none" stroke="var(--ink)" stroke-width="1"/></svg>
          www.coastlinepremierretreats.example
        </li>
      </ul>
    </div>

    <div class="logo-row">
      <span class="mark" aria-hidden="true"></span>
      <span class="brand-name">Coastline Premier Retreats</span>
    </div>

    <p class="tagline">Luxury Hotel &amp; Resort Email Marketing</p>
  </section>

</main>
</body>
</html>
```